The Velvet Magpie business card

I need a business card for my makeup artist business. I specialise in bridal, glamour, formal and special occasion makeup.
I am a mobile makeup artist who caters for every from nowra to sydney.
I do the following services:
Bridal makeup
airbrush makeup
special occasion
formals
hens nights/ girls night
makeup lesson
makeup for all ages from flower girl to Nanna of the bride!
photoshoot makeup
SPFX

I would like the card to portray a very professional sleek makeup business. I would also like another version of the card directed especially towards brides.

Please see my website to understand colours etc www.thevelvetmagpie-example.com

The Velvet Magpie
Professional Makeup Artist
Lorraine Kedby
0491802643
info@thevelvetmagpie-example.com
www.thevelvetmagpie-example.com
www.facebook.com/thevelvetmagpie

```html
<!DOCTYPE html>
<html lang="en">
<head>
<meta charset="utf-8">
<title>The Velvet Magpie – Business Card</title>
<link rel="stylesheet" href="https://fonts.googleapis.com/css2?family=Oswald:wght@300;400;500&family=Open+Sans:wght@400;700;800&display=swap">
<style>
  :root {
    --pink: #e0208f;
    --ink: #333333;
    --grey: #5a5a5a;
    --grey-soft: #b9b9b9;
    --paper: #ffffff;
    --backdrop: #ecebe8;
  }
  * { box-sizing: border-box; margin: 0; padding: 0; }
  html, body { width: 1200px; height: 913px; overflow: hidden; }
  body {
    background: var(--backdrop);
    position: relative;
    font-family: "Oswald", sans-serif;
    color: var(--ink);
  }
  .card {
    position: absolute;
    width: 540px;
    height: 320px;
    background: var(--paper);
    border-radius: 16px;
    overflow: hidden;
    box-shadow: 0 10px 28px rgba(0,0,0,.18);
  }
  .card-front { left: 50px; top: 120px; }
  .card-back { left: 610px; top: 470px; }
  .card-art { position: absolute; inset: 0; }

  /* front */
  .brand-name {
    position: absolute; left: 30px; top: 72px;
    font-family: "Oswald", sans-serif; font-weight: 400;
    font-size: 32px; letter-spacing: 2px; text-transform: uppercase;
    color: var(--pink); white-space: nowrap;
  }
  .contact-list { position: absolute; left: 32px; top: 168px; list-style: none; }
  .contact-list li {
    display: flex; align-items: center; gap: 9px;
    font-size: 14px; font-weight: 400; height: 24px; color: var(--ink);
    white-space: nowrap;
  }
  .contact-list li:first-child { font-size: 17px; }
  .contact-icon { width: 14px; height: 14px; flex: none; }
  .holder {
    position: absolute; right: 26px; top: 196px; text-align: right;
    color: var(--paper); font-family: "Open Sans", sans-serif;
  }
  .holder-name { font-size: 18px; font-weight: 800; }
  .holder-role { font-family: "Oswald", sans-serif; font-size: 14px; font-weight: 300; margin-top: 2px; }

  /* back */
  .service-list { position: absolute; left: 30px; top: 82px; list-style: none; width: 250px; }
  .service-list li {
    font-family: "Open Sans", sans-serif; font-weight: 700; font-size: 13px;
    line-height: 20px; color: var(--ink); padding-left: 20px; position: relative;
  }
  .service-list li::before {
    content: "»"; position: absolute; left: 0; color: var(--pink); font-weight: 800;
  }
  .photo { position: absolute; border: 3px solid var(--pink); }
  .photo-party { left: 300px; top: 18px; width: 200px; height: 88px;
    background: linear-gradient(135deg, #c9c4c8, #5f5b8c 60%, #9a98a6); }
  .photo-eyes { left: 330px; top: 100px; width: 190px; height: 88px;
    background: linear-gradient(120deg, #d7b79c, #f0d8c4 55%, #b89478); }
  .photo-lips { left: 300px; top: 192px; width: 218px; height: 96px;
    background: linear-gradient(120deg, #c9a086, #f3dccb 55%, #e8c9a8); }
</style>
</head>
<body>

<section class="card card-front" aria-label="Business card front">
  <svg class="card-art" viewBox="0 0 540 320" width="540" height="320">
    <rect class="ornament-area" x="410" y="0" width="130" height="48" fill="#eeeeee" role="img" aria-label="Faint grey swirl ornament"/>
    <path class="pink-wave" d="M540,60 L540,320 L190,320 C300,300 330,225 370,165 C410,110 460,80 540,60 Z" fill="var(--pink)"/>
    <path class="swoosh-dark" d="M130,318 C280,295 315,218 355,160 C400,100 455,70 540,50" fill="none" stroke="var(--grey)" stroke-width="8"/>
    <path class="swoosh-light" d="M160,314 C298,298 330,225 365,172 C410,114 462,86 540,68" fill="none" stroke="var(--grey-soft)" stroke-width="3"/>
  </svg>

  <div class="brand-name">The Velvet Magpie</div>

  <ul class="contact-list">
    <li>
      <svg class="contact-icon" viewBox="0 0 16 16"><path d="M3 2 L6 2 L7 5 L5 6.5 C6 8.5 7.5 10 9.5 11 L11 9 L14 10 L14 13 C8 14 2 8 3 2 Z" fill="var(--pink)"/></svg>
      0491802643
    </li>
    <li>
      <svg class="contact-icon" viewBox="0 0 16 16"><rect x="1" y="3" width="14" height="10" fill="var(--pink)"/><path d="M1 3 L8 9 L15 3" fill="none" stroke="#fff" stroke-width="1.3"/></svg>
      info@thevelvetmagpie-example.com
    </li>
    <li>
      <svg class="contact-icon" viewBox="0 0 16 16"><circle cx="8" cy="8" r="7" fill="var(--pink)"/><path d="M1 8 H15 M8 1 C4 5 4 11 8 15 M8 1 C12 5 12 11 8 15" fill="none" stroke="#fff" stroke-width="1"/></svg>
      www.thevelvetmagpie-example.com
    </li>
    <li>
      <svg class="contact-icon" viewBox="0 0 16 16"><rect x="1" y="1" width="14" height="14" fill="var(--pink)"/></svg>
      /thevelvetmagpie
    </li>
  </ul>

  <div class="holder">
    <div class="holder-name">Lorraine Kedby</div>
    <div class="holder-role">Professional Makeup Artist</div>
  </div>
</section>

<section class="card card-back" aria-label="Business card back">
  <svg class="card-art" viewBox="0 0 540 320" width="540" height="320">
    <path class="pink-panel" d="M290,0 H540 V320 H522 V205 H290 Z" fill="var(--pink)"/>
  </svg>
  <div class="photo photo-party" role="img" aria-label="Photo of a bridal party holding bouquets"></div>
  <div class="photo photo-eyes" role="img" aria-label="Photo of eye makeup being applied"></div>
  <div class="photo photo-lips" role="img" aria-label="Photo of lipstick being applied"></div>

  <ul class="service-list">
    <li>Formals</li>
    <li>Bridal makeup</li>
    <li>Airbrush makeup</li>
    <li>Special occasion</li>
    <li>Hens nights/ Girls night</li>
    <li>Makeup lesson</li>
    <li>Photoshoot makeup</li>
    <li>SPFX</li>
    <li>Makeup for all ages from flower girl to Nanna of the bride!</li>
  </ul>
</section>

</body>
</html>
```